Freelance business trainer needs a new business card

My business is called Brontlearn. I provide training in the workplace on management, coaching and mentoring, and customer service topics for a variety of businesses, colleges and private training providers, and teach on management programs. I need a professional but eye catching business card. Business colours grey and orange. My name Marion Tadwick; Tel 07382 415067; email mtadwick@brontlearn.co.uk; website www.brontlearn.co.uk.
Happy to have some sort of logo on front and details on back or all on one side
Target Market(s)
SME businesses and colleges - workshops i run are for adults in the workplace
Industry/Entity Type
Training
Look and feel

```html
<!DOCTYPE html>
<html lang="en">
<head>
<meta charset="utf-8">
<title>Brontlearn Business Card</title>
<link href="https://fonts.googleapis.com/css2?family=Montserrat:wght@500;600;700;800&display=swap" rel="stylesheet">
<style>
  :root {
    --orange: #f7941d;
    --ink: #2f2f2f;
    --grey: #555555;
    --paper: #ffffff;
    --backdrop: #e9e9e9;
  }
  * { margin: 0; padding: 0; box-sizing: border-box; }
  html, body {
    width: 1200px;
    height: 606px;
    overflow: hidden;
  }
  body {
    background: var(--backdrop);
    font-family: "Montserrat", Arial, sans-serif;
    color: var(--ink);
    position: relative;
  }
  .card {
    position: absolute;
    top: 148px;
    width: 520px;
    height: 310px;
    background: var(--paper);
    box-shadow: 0 10px 28px rgba(0, 0, 0, 0.18);
    overflow: hidden;
  }
  .card--back { left: 50px; }
  .card--front { left: 630px; }
  .card__bands {
    position: absolute;
    inset: 0;
    width: 100%;
    height: 100%;
  }
  .band { fill: var(--orange); }

  .brand { position: absolute; }
  .brand__name {
    display: block;
    font-weight: 800;
    color: var(--orange);
    line-height: 1;
    letter-spacing: -0.5px;
  }
  .brand__tagline {
    display: block;
    font-weight: 600;
    color: var(--orange);
    line-height: 1.2;
  }

  .card--back .brand {
    top: 40px;
    right: 34px;
    text-align: right;
  }
  .card--back .brand__name { font-size: 30px; }
  .card--back .brand__tagline { font-size: 8.5px; margin-top: 4px; }

  .holder {
    position: absolute;
    top: 112px;
    right: 34px;
    text-align: right;
  }
  .holder__name {
    font-size: 15px;
    font-weight: 700;
    color: var(--orange);
    letter-spacing: 0.3px;
  }
  .holder__role {
    font-size: 11px;
    font-weight: 500;
    color: var(--grey);
    margin-top: 1px;
  }

  .contact-list {
    position: absolute;
    left: 54px;
    top: 196px;
    list-style: none;
  }
  .contact-list li {
    font-size: 11px;
    font-weight: 700;
    color: var(--ink);
    height: 30px;
    line-height: 18px;
    letter-spacing: 0.3px;
  }

  .card--front .brand {
    left: 0;
    right: 0;
    top: 112px;
    text-align: center;
  }
  .card--front .brand__name { font-size: 58px; }
  .card--front .brand__tagline { font-size: 14px; margin-top: 8px; }
</style>
</head>
<body>

  <section class="card card--back" aria-label="Business card, back">
    <svg class="card__bands" viewBox="0 0 520 310" aria-hidden="true">
      <rect class="band" x="0" y="0" width="520" height="5"/>
      <path class="band" d="M190 0 H520 V16 H224 Q208 16 198 6 Z"/>
      <rect class="band" x="0" y="305" width="520" height="5"/>
      <path class="band" d="M118 310 H520 V291 H150 Q134 291 126 300 Z"/>
      <rect class="band" x="-8" y="186" width="44" height="104" rx="7"/>
      <!-- phone -->
      <rect x="12" y="196" width="11" height="17" rx="2" fill="none" stroke="#fff" stroke-width="1.8"/>
      <line x1="15.5" y1="209.5" x2="19.5" y2="209.5" stroke="#fff" stroke-width="1.5"/>
      <!-- mail -->
      <rect x="10" y="230" width="16" height="11" rx="1" fill="none" stroke="#fff" stroke-width="1.8"/>
      <path d="M10.5 231 L18 237 L25.5 231" fill="none" stroke="#fff" stroke-width="1.6"/>
      <!-- globe -->
      <circle cx="18" cy="266" r="8" fill="none" stroke="#fff" stroke-width="1.8"/>
      <ellipse cx="18" cy="266" rx="3.5" ry="8" fill="none" stroke="#fff" stroke-width="1.3"/>
      <line x1="10" y1="266" x2="26" y2="266" stroke="#fff" stroke-width="1.3"/>
    </svg>

    <div class="brand">
      <span class="brand__name">Brontlearn</span>
      <span class="brand__tagline">Professional Workplace Training Services</span>
    </div>

    <div class="holder">
      <p class="holder__name">Marion Tadwick</p>
      <p class="holder__role">CEO</p>
    </div>

    <ul class="contact-list">
      <li class="contact-list__phone">07382 415067</li>
      <li class="contact-list__email">mtadwick@brontlearn.co.uk</li>
      <li class="contact-list__web">www.brontlearn.co.uk</li>
    </ul>
  </section>

  <section class="card card--front" aria-label="Business card, front">
    <svg class="card__bands" viewBox="0 0 520 310" aria-hidden="true">
      <rect class="band" x="0" y="0" width="520" height="5"/>
      <path class="band" d="M200 0 H520 V18 H234 Q216 18 206 7 Z"/>
      <rect class="band" x="0" y="305" width="520" height="5"/>
      <path class="band" d="M0 310 V292 H366 Q384 292 394 302 L400 310 Z"/>
    </svg>

    <div class="brand">
      <span class="brand__name">Brontlearn</span>
      <span class="brand__tagline">Professional Workplace Training Services</span>
    </div>
  </section>

</body>
</html>
```